Tarvel Kite Corporate Site Template/Blog Design

Company Info: Tarvel Kite Robotics is a San Francisco based start-up and spin-off of Halvern Drury University Robotics Institute. Our mission is to transform the consumer experience through personal robotics technology.

Our first public brand, uPickGizmos.example (UPG), used these technologies to develop engaging toy and gaming category innovations that enhance the way children play and interact with new technologies.

This assignment is about the Tarvel Kite Robotic corporate identity and not about UPG

The company is transitioning to include higher end consumer electronics and personal robotics products lines within the next few years, and we would like to establish a more formal corporate identity. Attached please find a user flow of the design needed, as well as our current logo.

High Res .EPS Link below:

https://tkrobotics.filevault.example/shared/static/a730cbe12fd9931e27ab.eps

Design Vision: Tarvel Kite Robotics is in search of a simple, clean and easily updateable corporate website with an integrated blog. The company's current public profile is primarily UPG with an emphasis our children's toy lines Wudle and Clankoras. Although you should be aware of these toy sites, please do not let them influence your design. What we are looking for is more of a blend of scientific and cool.

We would like to see a site template and design that is clean and approachable. It also needs to be able to support a CMS platform as we need the ability to allow our marketing team to update and manage content as well as add additional features such as video and ecommerce in the future as the company grows. These designs should also work well with Facebook and Twitter.

Attached is an image of our corporate card. The current color scheme is very basic but the design should complement them.

The final design and layout should communicate a sleek, innovative and technologically saavy consumer electronics and personal robotics company. Again, we are a consumer oriented organization but the key audiences for this site will be investors, media, retail and biz dev partners, and potential employees

Target Market(s)

Investors, Biz dev and other partners, retail, Media, employees. Consumers secondary

Industry/Entity Type

Electronics

Requirements
Must have
• The site must have all of the tabs that we have identified in the attached user flow.

The design must be able to support a backend content management system. We currently have an upgraded PageRo account, and can provide access if needed but will soon transition to our own site. we are open to your recommendations. Our objective is to be able to easily update the content without relying on a developer.

Font should be sleek. And not bubbly.
Nice to have
• Clean site design. Simple layouts. A blend between scientific and cool. Easy to navigate tabs and sub tabs. forward thinking imagery

Should not have
• Nothing complex on the Homepage- should be very simple. No cartoonish robots, bright colors. Little or no use of humans in stock photos. No competative products or copy. Toys should be under product tabs, and not featured on the homepage as in our initial design efforts we felt that the two were aesthetically polarizing. Just to confirm, the Tarvel Kite Corporate site should serve more as the parent site, and the toy lines should stay under the sub navs on the product page.

```html
<!DOCTYPE html>
<html lang="en">
<head>
<meta charset="utf-8">
<title>Tarvel Kite Robotics Institute</title>
<link rel="stylesheet" href="https://fonts.googleapis.com/css2?family=Arimo:wght@400;700&family=PT+Sans:ital,wght@0,400;0,700;1,700&family=Noto+Sans:wght@400;700&family=Ubuntu:wght@400&display=swap">
<style>
:root{
  --navy:#1d4669;
  --navy-dark:#16384f;
  --ink:#222;
  --muted:#555;
  --brown:#8a6a3f;
  --sand:#e8e4df;
  --sand-light:#f2f0ed;
  --rule:#c9c9c9;
  --steel:#4a7390;
  --steel-dark:#23374a;
  --white:#fff;
  --field:#fbfbfb;
}
*{box-sizing:border-box;margin:0;padding:0}
html,body{width:1142px;height:1200px;overflow:hidden;background:var(--white);font-family:Arimo,Arial,sans-serif;color:var(--ink)}
.page{position:relative;width:1142px;height:1200px}
.topbar{position:absolute;left:0;top:0;width:100%;height:6px;background:var(--navy-dark)}

.brand{position:absolute;left:94px;top:26px;display:flex;align-items:flex-end;height:42px}
.brand-name{font-family:Ubuntu,sans-serif;font-size:26px;color:var(--navy);line-height:1;padding-bottom:10px}
.brand-sep{width:2px;height:40px;background:var(--rule);margin:0 5px 0 8px}
.brand-tag{font-size:12px;color:var(--brown);padding-bottom:2px}

.search{position:absolute;left:867px;top:21px;width:174px;height:24px;background:#e4e4e6;border:1px solid #c6c6c8;border-left:2px solid #a9a9ab;font-size:11px;color:#777;padding:5px 5px}
.search svg{position:absolute;right:6px;top:3px}
.head-rule{position:absolute;left:326px;top:61px;width:715px;height:2px;background:#bdbdbd}

.nav{position:absolute;left:327px;top:75px;width:721px;display:flex;justify-content:space-between;list-style:none;height:37px;align-items:center;font-size:15px;letter-spacing:.1px}
.nav li{line-height:37px;color:#222;white-space:nowrap}
.nav .active{background:var(--navy);color:var(--white);width:77px;text-align:center}
.nav-rule{position:absolute;left:92px;top:125px;width:960px;height:2px;background:#e7e7e7}

.slider{position:absolute;left:107px;top:139px;width:931px;height:313px;border:1px solid #d6d6d6}
.slide{position:absolute;left:5px;top:5px;width:919px;height:301px;background:var(--navy);border-radius:8px 0 0 0}
.slide-photo{position:absolute;left:30px;top:2px;width:333px;height:293px;background:linear-gradient(160deg,#e9ecef,#c5cbd2 60%,#b8a48a)}
.slide-copy{position:absolute;left:451px;top:38px;width:344px;font-family:"Noto Sans",sans-serif;font-size:12px;line-height:16.3px;color:#eef2f6;text-align:justify}
.slide-btn{position:absolute;left:518px;top:169px;width:239px;height:42px;border-radius:5px;background:linear-gradient(#fff,#d9d9d9);border:1px solid #888;box-shadow:0 1px 3px rgba(0,0,0,.4);font-family:"PT Sans",sans-serif;font-weight:700;font-size:17px;color:#222;display:flex;align-items:center;padding-left:15px;gap:10px;white-space:nowrap}
.slide-arrow{position:absolute;top:113px;width:20px;height:38px;background:var(--white)}
.slide-arrow.prev{left:-6px;border-radius:0 19px 19px 0}
.slide-arrow.next{right:-6px;border-radius:19px 0 0 19px}
.slide-arrow svg{position:absolute;top:13px}

.band{position:absolute;left:0;top:475px;width:100%;height:307px;background:var(--sand)}
.section-title{font-family:"PT Sans",sans-serif;font-style:italic;font-weight:700;font-size:17px;color:var(--navy);white-space:nowrap}
.research{position:absolute;left:108px;top:485px;width:560px}
.research-list{list-style:none;margin-top:10px}
.research-list li{position:relative;font-size:12px;line-height:16px;color:#222;height:49.5px;padding-top:5px;border-bottom:1px dashed #c8c2ba}
.research-list li:last-child{border-bottom:0}
.more{font-size:10px;color:#6b6b6b}
.research-list .more{position:absolute;right:0;top:22px}

.quote{position:absolute;left:747px;top:507px;width:303px;height:275px;background:var(--sand-light)}
.quote-title{position:absolute;left:768px;top:483px}
.quote-arrow{position:absolute;left:1013px;top:479px;z-index:2}
.field{position:absolute;left:0;width:100%;font-size:11px;color:#555}
.field label{position:absolute;right:238px;top:9px;white-space:nowrap}
.field span{position:absolute;left:75px;width:209px;height:30px;background:var(--field);border:1px solid #dcdcdc;border-radius:4px}
.submit{position:absolute;left:176px;top:224px;width:106px;height:34px;border-radius:4px;background:linear-gradient(#5a5a5a,#141414);border:1px solid #000;color:var(--white);font-family:"PT Sans",sans-serif;font-style:italic;font-weight:700;font-size:16px;text-align:center;line-height:32px}

.col{position:absolute;top:812px;width:280px;border-left:2px solid #c7c7c7;padding-left:9px}
.col h3{font-family:Arimo,sans-serif;font-weight:700;font-size:15px;color:var(--brown);margin-bottom:6px}
.col p{font-size:11.3px;line-height:17px;color:#444;text-align:justify}
.col .item{position:relative;margin-bottom:8px}
.col .item .more{position:absolute;right:0;bottom:0;color:#8a6a3f}

.footer{position:absolute;left:0;top:1020px;width:100%;height:151px;background:var(--steel);box-shadow:inset 0 0 40px var(--steel-dark)}
.partners-title{position:absolute;left:97px;top:33px;font-size:12px;color:var(--white);letter-spacing:.3px;white-space:nowrap}
.partners-rule{position:absolute;left:270px;top:40px;width:232px;height:2px;background:#cfd9e1}
.logos{position:absolute;left:118px;top:57px;display:flex;gap:7px}
.logos li{list-style:none;width:68px;height:44px;background:#d6d6d6;font-size:11px;color:#999;padding:8px 0 0 14px;line-height:14px}
.logo-nav{position:absolute;top:72px}
.partner-feature{position:absolute;left:699px;top:43px;width:342px;height:65px;background:var(--white);display:flex;align-items:center;justify-content:center;text-align:center;font-family:"PT Sans",sans-serif;font-weight:700;font-size:19px;line-height:20px;color:#111}

.bottom-links{position:absolute;left:97px;top:1181px;font-size:10px;color:#333;white-space:nowrap}
.copyright{position:absolute;left:986px;top:1180px;font-size:10px;color:#333}
</style>
</head>
<body>
<div class="page">
  <div class="topbar"></div>

  <div class="brand">
    <span class="brand-name">Tarvel Kite</span>
    <span class="brand-sep"></span>
    <span class="brand-tag">Robotics institute</span>
  </div>

  <div class="search">Quick search
    <svg width="22" height="16" viewBox="0 0 22 16"><circle cx="8" cy="7" r="5" fill="#f4f6f8" stroke="#7a8a99" stroke-width="1.5"/><line x1="12" y1="10" x2="20" y2="14" stroke="#555" stroke-width="2"/></svg>
  </div>
  <div class="head-rule"></div>

  <ul class="nav">
    <li class="active">HOME</li>
    <li>ABOUT US</li>
    <li>RESEARCH</li>
    <li>EDUCATION</li>
    <li>PEOPLE</li>
    <li>CAREER</li>
    <li>EVENTS</li>
    <li>CONTACT US</li>
  </ul>
  <div class="nav-rule"></div>

  <div class="slider">
    <div class="slide">
      <div class="slide-photo" role="img" aria-label="Photograph of a human hand shaking a robotic hand"></div>
      <p class="slide-copy">Lorem Ipsum is simply dummy text of the printing and typesetting industry. Lorem Ipsum has been the industry's standard dummy text ever since the 1500s, when an unknown printer took a galley of type and scrambled it to make a type specimen book.</p>
      <div class="slide-btn">Learn more about this
        <svg width="20" height="14" viewBox="0 0 20 14"><path d="M0 4h11V0l9 7-9 7v-4H0z" fill="#c0392b"/></svg>
      </div>
    </div>
    <div class="slide-arrow prev"><svg width="12" height="12" viewBox="0 0 12 12" style="left:3px"><path d="M10 6H2M5 3L2 6l3 3" stroke="#aaa" stroke-width="1.5" fill="none"/></svg></div>
    <div class="slide-arrow next"><svg width="12" height="12" viewBox="0 0 12 12" style="left:5px"><path d="M2 6h8M7 3l3 3-3 3" stroke="#aaa" stroke-width="1.5" fill="none"/></svg></div>
  </div>

  <div class="band"></div>

  <section class="research">
    <h2 class="section-title">Research....!</h2>
    <ul class="research-list">
      <li>Contrary to popular belief, Lorem Ipsum is not simply random text. It has roots in a piece of classical Latin literature from 45 BC.<span class="more">more</span></li>
      <li>Contrary to popular belief, Lorem Ipsum is not simply random text. It has roots in a piece of classical Latin literature from 45 BC.<span class="more">more</span></li>
      <li>Contrary to popular belief, Lorem Ipsum is not simply random text. It has roots in a piece of classical Latin literature from 45 BC.<span class="more">more</span></li>
      <li>Contrary to popular belief, Lorem Ipsum is not simply random text. It has roots in a piece of classical Latin literature from 45 BC.</li>
      <li>Contrary to popular belief, Lorem Ipsum is not simply random text. It has roots in a piece of classical Latin literature from 45 BC.<span class="more">more</span></li>
    </ul>
  </section>

  <h2 class="section-title quote-title">Quick quote....!</h2>
  <form class="quote">
    <div class="field" style="top:23px"><label>Name :</label><span></span></div>
    <div class="field" style="top:64px"><label>Email Id :</label><span></span></div>
    <div class="field" style="top:103px"><label>Mobile :</label><span></span></div>
    <div class="field" style="top:142px"><label style="top:3px">Queries :</label><span style="height:67px"></span></div>
    <div class="submit">Submit</div>
  </form>
  <svg class="quote-arrow" width="30" height="44" viewBox="0 0 30 44">
    <g fill="#2a9fd6"><rect x="9" y="0" width="4" height="4"/><rect x="15" y="0" width="4" height="4"/><rect x="9" y="6" width="4" height="4"/><rect x="15" y="6" width="4" height="4"/><rect x="9" y="12" width="4" height="4"/><rect x="15" y="12" width="4" height="4"/></g>
    <path d="M8 18h12v8h8L14 42 0 26h8z" fill="#4cc0ea" stroke="#1b86b8"/>
  </svg>

  <section class="col" style="left:100px">
    <h3>About Us</h3>
    <p>Lorem ipsum dolor sit amet, consectetur adipisicing elit, sed do eiusmod tempor incididunt ut labore et dolore magna aliqua. Ut enim ad minim veniam, quis nostrud exercitation ullamco laboris nisi ut aliquip ex ea commodo consequat. Duis aute irure dolor in reprehenderit in voluptate velit esse cillum dolore eu fugiat nulla pariatur. Excepteur sint occaecat cupidatat non proident, sunt in culpa qui officia deserunt mollit anim id est laborum.</p>
  </section>

  <section class="col" style="left:429px">
    <h3>New Events</h3>
    <div class="item"><p>Lorem ipsum dolor sit amet, consectetur adipisicing elit, sed do eiusmod tempor incididunt ut labore et dolore magna aliqua.</p><span class="more">more</span></div>
    <div class="item"><p>Lorem ipsum dolor sit amet, consectetur adipisicing elit, sed do eiusmod tempor incididunt ut labore et dolore magna aliqua.</p><span class="more">more</span></div>
    <div class="item"><p>Lorem ipsum dolor sit amet, consectetur adipisicing elit, sed do eiusmod tempor incididunt ut labore et dolore magna aliqua.</p><span class="more">more</span></div>
  </section>

  <section class="col" style="left:764px">
    <h3>Academic Programme</h3>
    <p>Lorem ipsum dolor sit amet, consectetur adipisicing elit, sed do eiusmod tempor incididunt ut labore et dolore magna aliqua. Ut enim ad minim veniam, quis nostrud exercitation ullamco laboris nisi ut aliquip ex ea commodo consequat. Duis aute irure dolor in reprehenderit in voluptate velit esse cillum dolore eu fugiat nulla pariatur. Excepteur sint occaecat cupidatat non proident, sunt in culpa qui officia deserunt mollit anim id est laborum.</p>
  </section>

  <footer class="footer">
    <div class="partners-title">INVESTORS AND PARTNERS</div>
    <div class="partners-rule"></div>
    <svg class="logo-nav" style="left:100px" width="14" height="14" viewBox="0 0 14 14"><circle cx="7" cy="7" r="6" fill="#e8e8e8" stroke="#888"/><path d="M8.5 4L5 7l3.5 3z" fill="#555"/></svg>
    <ul class="logos">
      <li>Client Logo 1</li>
      <li>Client Logo 2</li>
      <li>Client Logo 3</li>
      <li>Client Logo 4</li>
      <li>Client Logo 5</li>
    </ul>
    <svg class="logo-nav" style="left:496px" width="14" height="14" viewBox="0 0 14 14"><circle cx="7" cy="7" r="6" fill="#e8e8e8" stroke="#888"/><path d="M5.5 4L9 7l-3.5 3z" fill="#555"/></svg>
    <div class="partner-feature">Halvern Drury University<br>Robotics Institute</div>
  </footer>

  <div class="bottom-links">Portals &nbsp;|&nbsp; Facutlies &nbsp;|&nbsp; Students &nbsp;|&nbsp; Achievements</div>
  <div class="copyright">Copyright</div>
</div>
</body>
</html>
```